Stylish new business card needed!

Hello everyone! I am in need of a new business card design for an alarm company here in Hurricane WV. I have all fonts, color codes and logos provided for you use! We are a young company and like the style of a clean sleek looking business card. Would like it double sided, one side holding the logo and the other with your design!
Target Market(s)
The people that are looking for the newest tech for home automation and security
Industry/Entity Type
Alarm services; Home automation
Contact Information for Business Card
Name of person; position (Sales; Installer); Phone Number (555.418.7260); Employee cell Number; Website (www.GuardedByVelk.example); Employee Email; Double sided
Look and feel
Each slider illustrates characteristics of the customer's brand and the style your logo design should communicate.

```html
<!DOCTYPE html>
<html lang="en">
<head>
<meta charset="utf-8">
<title>Velk Business Card</title>
<link href="https://fonts.googleapis.com/css2?family=Montserrat:wght@400;600;800&family=Arimo:wght@400&display=swap" rel="stylesheet">
<style>
  :root {
    --stage: #141414;
    --card: #2a2a2a;
    --card-deep: #232323;
    --accent: #f47a2c;
    --ink: #f2f2f2;
    --muted: #bdbdbd;
  }
  * { box-sizing: border-box; margin: 0; padding: 0; }
  html, body { width: 1200px; height: 963px; overflow: hidden; }
  body {
    background: var(--stage);
    display: flex;
    align-items: center;
    justify-content: center;
    gap: 60px;
    font-family: "Arimo", Arial, sans-serif;
  }
  .card {
    position: relative;
    width: 520px;
    height: 297px;
    border-radius: 18px;
    background: radial-gradient(ellipse at 40% 40%, #303030, var(--card-deep));
    box-shadow: 0 4px 0 var(--accent), 0 20px 40px rgba(0,0,0,.6);
    overflow: hidden;
  }
  /* front */
  .brand {
    position: absolute;
    left: 40px;
    top: 42px;
  }
  .brand-row { display: flex; align-items: center; gap: 12px; }
  .brand-dot {
    width: 40px; height: 40px; border-radius: 50%;
    background: var(--accent);
  }
  .brand-name {
    font-family: "Montserrat", sans-serif;
    font-weight: 400;
    font-size: 64px;
    line-height: 1;
    letter-spacing: 2px;
    color: var(--ink);
  }
  .brand-tagline {
    margin-top: 8px;
    font-family: "Montserrat", sans-serif;
    font-weight: 800;
    font-size: 8.5px;
    letter-spacing: .6px;
    color: var(--accent);
  }
  .contact {
    position: absolute;
    right: 38px;
    bottom: 30px;
    width: 240px;
  }
  .person-name {
    font-family: "Montserrat", sans-serif;
    font-weight: 800;
    font-size: 19px;
    color: var(--accent);
    letter-spacing: .3px;
  }
  .person-role { font-size: 14px; color: var(--ink); margin-top: 2px; }
  .icons { display: flex; gap: 8px; margin: 12px 0 10px; }
  .icon {
    width: 24px; height: 24px; border-radius: 50%;
    border: 1.5px solid var(--accent);
    display: flex; align-items: center; justify-content: center;
  }
  .icon svg { width: 13px; height: 13px; stroke: var(--accent); fill: none; stroke-width: 1.6; }
  .contact-line { font-size: 13.5px; color: var(--ink); line-height: 1.55; }
  /* back */
  .back-pattern { position: absolute; inset: 0; background: linear-gradient(135deg, #2c2c2c, #242424); }
  .back-mark {
    position: absolute;
    right: 40px;
    bottom: 34px;
    display: flex; align-items: center; gap: 8px;
  }
  .back-mark .brand-dot { width: 22px; height: 22px; }
  .back-mark .brand-name { font-size: 34px; }
</style>
</head>
<body>
  <section class="card card-front">
    <div class="brand">
      <div class="brand-row">
        <span class="brand-dot"></span>
        <span class="brand-name">VELK</span>
      </div>
      <p class="brand-tagline">AUTOMATION AND SECURITY SERVICES</p>
    </div>
    <div class="contact">
      <p class="person-name">DANIEL HARPER</p>
      <p class="person-role">Sales / Installer</p>
      <div class="icons">
        <span class="icon"><svg viewBox="0 0 16 16"><path d="M4 2l2 3-1.5 1.5a8 8 0 0 0 5 5L11 10l3 2-1 2.5C7 14 2 9 1.5 3z"/></svg></span>
        <span class="icon"><svg viewBox="0 0 16 16"><rect x="2" y="4" width="12" height="8" rx="1"/><path d="M2 4l6 5 6-5"/></svg></span>
        <span class="icon"><svg viewBox="0 0 16 16"><circle cx="8" cy="8" r="6"/><path d="M2 8h12M8 2c3 3 3 9 0 12M8 2c-3 3-3 9 0 12"/></svg></span>
      </div>
      <p class="contact-line">555.418.7260</p>
      <p class="contact-line">info@GuardedByVelk.example</p>
      <p class="contact-line">www.GuardedByVelk.example</p>
    </div>
  </section>

  <section class="card card-back">
    <div class="back-pattern" role="img" aria-label="Tone-on-tone embossed repeat of the company name across the card"></div>
    <div class="back-mark">
      <span class="brand-dot"></span>
      <span class="brand-name">VELK</span>
    </div>
  </section>
</body>
</html>
```